Polystyrene Recycling Material Flow

We need a diagram styled as an infographic that shows how polystyrene foam is recycled starting with a manufactured product, moving through the distribution process, waste material collection and reincorporation back into manufacturing. This is accomplished in different ways once the material is collected which needs to be clearly evident. The most important thing is for it to be simple enough to understand while still having a stylish look. The design can be with or without vector images or photography to depict the different stages. We are providing a very rudimentary 'sketch' of the information points and movement flow. Please see www.foamtradecouncil.org (resources) to view our literature branding. The RGB & CMYK are attached.

Target Market(s)

Government Agencies, Brand Owners, Retailers, Recycling Industry

Industry/Entity Type

Packaging, Recycling, Manufacturing

Font styles to use
Sans Serif

Requirements
Must have
• Easy to Understand
Nice to have
• Images - either photography or vector illustrations - are optional. We have provided examples of both to show what could be used but are not required. Substituting your own interpretation of imagery is encouraged.
Should not have
• Outdated look.

```html
<!DOCTYPE html>
<html lang="en">
<head>
<meta charset="utf-8">
<title>Polystyrene Recycling Material Flow</title>
<link href="https://fonts.googleapis.com/css2?family=Roboto:wght@400;500;700&display=swap" rel="stylesheet">
<style>
:root{
  --orange:#F5A623;
  --gold:#BF9012;
  --gold-light:#CFA533;
  --gold-text:#B8860B;
  --brown:#6B2A12;
  --ink:#111111;
  --grey:#E6E6E6;
  --olive:#A7A61B;
  --maroon:#5A2418;
  --slate:#5B7F9E;
}
*{box-sizing:border-box;margin:0;padding:0}
html,body{width:1200px;height:677px;overflow:hidden;background:#fff;font-family:"Roboto",Arial,sans-serif;color:var(--ink)}
.canvas{position:relative;width:1200px;height:677px}
.flow-lines{position:absolute;left:0;top:0}
.abs{position:absolute}
.section-title{left:89px;top:206px;transform:translate(-50%,-50%) rotate(-90deg);font-weight:700;font-size:17px;letter-spacing:.3px;white-space:nowrap}
.art{position:absolute;border-radius:6px}
.source-pill{position:absolute;height:31px;border-radius:16px;display:flex;align-items:center;box-shadow:0 2px 5px rgba(0,0,0,.12);background:#fff;overflow:hidden}
.source-pill .cap{width:45px;height:100%;display:flex;align-items:center;justify-content:center;border-radius:16px 0 0 16px}
.source-pill .cap span{width:12px;height:12px;border:1.5px solid #fff;border-radius:2px}
.source-pill .name{flex:1;text-align:center;font-weight:700;font-size:9.5px;background:#fff;height:100%;display:flex;align-items:center;justify-content:center;border-radius:16px;margin-left:-10px}
.municipal .cap{background:var(--olive)}
.manufacturing .cap{background:var(--maroon)}
.commercial .cap{background:var(--slate)}
.note{position:absolute;font-size:10.5px;white-space:nowrap}
.collection-ring{position:absolute;left:548px;top:189px;width:183px;height:78px;border:2px solid var(--orange);border-radius:40px}
.collection-core{position:absolute;left:564px;top:204px;width:152px;height:48px;border-radius:24px;background:#fff;box-shadow:0 2px 8px rgba(0,0,0,.15);display:flex;align-items:center;justify-content:center;font-weight:700;font-size:13px}
.stage{position:absolute;height:46px;border-radius:8px;background:var(--gold);display:flex;color:#fff;overflow:hidden}
.stage .cap{width:37px;background:var(--gold-light);display:flex;align-items:center;justify-content:center}
.stage .cap span{width:14px;height:14px;border:1.5px solid #fff;border-radius:2px}
.stage .name{flex:1;display:flex;align-items:center;justify-content:center;text-align:center;font-weight:500;font-size:11.5px;line-height:1.3}
.step{position:absolute;height:28px;border-radius:14px;background:#fff;display:flex;align-items:center;justify-content:center;font-weight:700;font-size:9.5px;white-space:nowrap}
.step.process{border:1.5px solid var(--brown);color:var(--brown)}
.step.output{border:1.5px solid var(--gold-text);color:var(--gold-text)}
</style>
</head>
<body>
<main class="canvas">
<svg class="flow-lines" width="1200" height="677" viewBox="0 0 1200 677">
  <defs>
    <marker id="tip" markerWidth="6" markerHeight="6" refX="5" refY="3" orient="auto"><path d="M0,0 L6,3 L0,6 Z" fill="#777"/></marker>
    <marker id="tip-dark" markerWidth="6" markerHeight="6" refX="5" refY="3" orient="auto"><path d="M0,0 L6,3 L0,6 Z" fill="#111"/></marker>
  </defs>
  <g fill="none" stroke="var(--orange)" stroke-width="2">
    <polyline points="225,607 225,634 56,634 56,67 640,67 640,189"/>
    <polyline points="336,106 336,92 624,92 624,189"/>
    <polyline points="897,548 897,600 1151,600 1151,92 656,92 656,189"/>
    <polyline points="631,267 631,316 402,316 402,338"/>
    <polyline points="648,267 648,316 896,316 896,338"/>
  </g>
  <g fill="var(--orange)">
    <circle cx="225" cy="607" r="3.5"/><circle cx="336" cy="106" r="3.5"/>
    <circle cx="624" cy="189" r="3.5"/><circle cx="640" cy="189" r="3.5"/><circle cx="656" cy="189" r="3.5"/>
    <circle cx="631" cy="267" r="3.5"/><circle cx="648" cy="267" r="3.5"/>
    <circle cx="402" cy="338" r="3.5"/><circle cx="896" cy="338" r="3.5"/><circle cx="897" cy="548" r="3.5"/>
  </g>
  <path d="M160,112 C130,112 140,200 115,206 C140,212 130,299 160,299" fill="none" stroke="var(--grey)" stroke-width="6"/>
  <g stroke="var(--brown)" stroke-width="1.2" fill="none">
    <polyline points="402,394 402,415"/>
    <polyline points="260,434 260,415 542,415 542,434"/>
    <polyline points="894,394 894,434"/>
  </g>
  <g fill="var(--brown)"><circle cx="260" cy="434" r="2.5"/><circle cx="542" cy="434" r="2.5"/><circle cx="894" cy="434" r="2.5"/></g>
  <g stroke="#777" stroke-width="1" marker-end="url(#tip)">
    <line x1="390" y1="127" x2="411" y2="118"/><line x1="390" y1="134" x2="411" y2="140"/>
    <line x1="394" y1="265" x2="411" y2="258"/><line x1="394" y1="275" x2="411" y2="281"/>
    <line x1="468" y1="366" x2="486" y2="359"/><line x1="468" y1="376" x2="486" y2="382"/>
    <line x1="939" y1="457" x2="960" y2="449"/><line x1="939" y1="465" x2="960" y2="472"/>
  </g>
  <g stroke="#111" stroke-width="1" marker-end="url(#tip-dark)">
    <line x1="259" y1="475" x2="259" y2="491"/><line x1="545" y1="475" x2="545" y2="495"/>
    <line x1="894" y1="475" x2="894" y2="491"/><line x1="259" y1="533" x2="259" y2="551"/>
  </g>
</svg>

<div class="abs section-title">EPS WASTE SOURCES</div>

<div class="art" role="img" aria-label="Green and orange wheeled recycling bins" style="left:172px;top:112px;width:68px;height:38px;background:linear-gradient(90deg,#2E7D32 45%,#F39C12 45%)"></div>
<div class="art" role="img" aria-label="Factory with smoking chimneys" style="left:177px;top:166px;width:62px;height:48px;background:linear-gradient(180deg,#B0BEC5,#E53935)"></div>
<div class="art" role="img" aria-label="Pile of bagged commercial waste" style="left:190px;top:236px;width:55px;height:58px;background:linear-gradient(180deg,#2E2E2E,#4CAF50 55%,#90A4AE)"></div>

<div class="source-pill municipal" style="left:255px;top:116px;width:134px"><div class="cap"><span></span></div><div class="name">MUNICIPAL WASTE</div></div>
<div class="source-pill manufacturing" style="left:255px;top:185px;width:161px"><div class="cap"><span></span></div><div class="name">MANUFACTURING WASTE</div></div>
<div class="source-pill commercial" style="left:255px;top:255px;width:139px"><div class="cap"><span></span></div><div class="name">COMMERCIAL WASTE</div></div>

<div class="note" style="left:420px;top:110px">Curbside Collection</div>
<div class="note" style="left:420px;top:133px">Drop-Off Centers</div>
<div class="note" style="left:421px;top:250px">Back Hauling</div>
<div class="note" style="left:421px;top:273px">Localized Delivery</div>

<div class="collection-ring"></div>
<div class="collection-core">COLLECTION</div>

<div class="art" role="img" aria-label="Converging coloured arrows" style="left:280px;top:348px;width:40px;height:45px;background:linear-gradient(135deg,#E53935,#4FC3F7 50%,#43A047 70%,#FBC02D)"></div>
<div class="stage" style="left:335px;top:348px;width:132px"><div class="cap"><span></span></div><div class="name">COMPACTION</div></div>
<div class="note" style="left:495px;top:352px">Extruded Ingot</div>
<div class="note" style="left:495px;top:375px">Hydrolic Compression</div>

<div class="stage" style="left:813px;top:348px;width:161px"><div class="cap"><span></span></div><div class="name">REGRIND - MOLDER<br>FACILITIES</div></div>
<div class="art" role="img" aria-label="Office buildings" style="left:991px;top:355px;width:40px;height:35px;background:linear-gradient(90deg,#FBC02D 40%,#1E88E5 40%)"></div>

<div class="art" role="img" aria-label="Recycling arrows symbol" style="left:148px;top:447px;width:29px;height:28px;background:#43A047;border-radius:50%"></div>
<div class="step process" style="left:186px;top:447px;width:148px">Recycled Content EPS Resin</div>
<div class="art" role="img" aria-label="Two fists pressing together" style="left:412px;top:445px;width:45px;height:30px;background:linear-gradient(90deg,#1E88E5,#F48FB1 30%,#E53935 50%,#F48FB1 70%,#1E88E5)"></div>
<div class="step process" style="left:468px;top:447px;width:149px">Extruded Rigid PS Pellet</div>
<div class="art" role="img" aria-label="Paper shredder" style="left:811px;top:448px;width:29px;height:26px;background:linear-gradient(180deg,#ECEFF1,#1E88E5)"></div>
<div class="step process" style="left:849px;top:447px;width:90px">Shredding</div>
<div class="note" style="left:969px;top:442px">Homogenization</div>
<div class="note" style="left:969px;top:465px">Mixing for Consistency</div>

<div class="art" role="img" aria-label="Blowing wind lines" style="left:117px;top:504px;width:35px;height:27px;background:linear-gradient(180deg,#90CAF9,#1E88E5)"></div>
<div class="step output" style="left:163px;top:505px;width:171px">Re-Pelletized With Blowing Agent</div>
<div class="art" role="img" aria-label="Computer monitor with settings" style="left:416px;top:495px;width:35px;height:36px;background:linear-gradient(180deg,#455A64,#90A4AE)"></div>
<div class="step output" style="left:468px;top:505px;width:149px">End Market Applications</div>
<div class="art" role="img" aria-label="Green recycling bin" style="left:802px;top:504px;width:25px;height:32px;background:#7CB342"></div>
<div class="step output" style="left:840px;top:508px;width:114px">Recycled Content</div>

<div class="art" role="img" aria-label="Cardboard shipping box" style="left:76px;top:563px;width:28px;height:32px;background:linear-gradient(135deg,#FFB74D,#E67E22)"></div>
<div class="step process" style="left:114px;top:565px;width:220px">Expanded Polystyrene Packaging &amp; Building</div>
</main>
</body>
</html>
```